Dental Practice Billboard Design

We are a newer dental practice in need of a simple but appealing billboard for our growing dental practice to attract new patients. The practice is owned by husband and wife dentists and is family friendly in a small town in Kentucky. We try to be very friendly and caring to our patients. Would prefer a blue background for the billboard and our tooth logo to be prominent. We are partial to the Patua One font used in the image below but please feel free to tweak it as you deem necessary. The shape of the uppercase D and lowercase g are why we like that font, so fonts with a similarly shaped “D” and “g” would work as well. Please include our phone number (555) 847-1390. Please see our website Harlowbrookdentistry.example for more info on the practice if needed. Thank you! Looking forward to seeing your creation.
Updates

The dimensions will be 12ft x 24ft (3.6576m x 7.3152m). Apologies for not including this in the original prompt. Thank you all for your submissions.

Industry/Entity Type

Dental

Font styles to use
Other font styles liked:
• Patua One

Colors
0054AA
0677BA
7BADD7
CADEEF
E8F1F8
0094D4
00A9DD
6FCCEA
C7EBF8
E9F6FB
00AB8E
00BBA5
67D7C9
C6EFE9
E9F9F6
59FF00
82FF00
B8FF75
E3FFCB
F4FFEA

Requirements
Must have
• Phone number, website, Logo, Practice name “Harlow Brook Dentistry”
Should not have
• A tagline or slogan

```html
<!DOCTYPE html>
<html lang="en">
<head>
<meta charset="UTF-8">
<title>Harlow Brook Dentistry – Billboard</title>
<link rel="stylesheet" href="https://fonts.googleapis.com/css2?family=Patua+One&display=swap">
<style>
  :root {
    --navy: #0b2a5e;
    --green: #17b31b;
    --green-light: #59d632;
    --white: #ffffff;
    --ink: #2b2b2b;
    --page: #ffffff;
  }
  * { box-sizing: border-box; margin: 0; padding: 0; }
  html, body {
    width: 1071px;
    height: 1200px;
    overflow: hidden;
    background: var(--page);
  }
  .billboard {
    position: absolute;
    left: 36px;
    top: 351px;
    width: 1000px;
    height: 498px;
    background: var(--navy);
    overflow: hidden;
    font-family: "Patua One", Georgia, serif;
    color: var(--white);
    box-shadow: 0 2px 6px rgba(0,0,0,0.25);
  }
  .practice-photo {
    position: absolute;
    left: 76px;
    top: 46px;
    width: 262px;
    height: 312px;
    border-radius: 40px 40px 110px 110px;
    border: 10px solid var(--white);
    border-right-color: var(--green);
    background: linear-gradient(160deg, #c9b8a4 0%, #eef0f2 45%, #e8ecef 70%, #1c1c22 100%);
  }
  .practice-name {
    position: absolute;
    left: 384px;
    top: 86px;
    line-height: 1;
  }
  .practice-name__main {
    display: block;
    font-size: 158px;
    letter-spacing: -1px;
  }
  .practice-name__sub {
    display: block;
    margin-top: 14px;
    margin-left: -20px;
    font-size: 64px;
  }
  .web-band {
    position: absolute;
    left: 0;
    top: 422px;
    width: 628px;
    height: 76px;
    background: var(--green);
    clip-path: polygon(0 0, 566px 0, 628px 76px, 0 76px);
    display: flex;
    align-items: center;
    padding-left: 32px;
    gap: 14px;
    font-size: 30px;
  }
  .phone-band {
    position: absolute;
    left: 584px;
    top: 437px;
    width: 416px;
    height: 61px;
    background: var(--white);
    clip-path: polygon(0 0, 416px 0, 416px 61px, 18px 61px);
    display: flex;
    align-items: center;
    padding-left: 40px;
    gap: 20px;
    font-size: 38px;
    color: var(--ink);
  }
  .icon { flex: none; display: block; }
</style>
</head>
<body>
  <main class="billboard">
    <div class="practice-photo" role="img" aria-label="Photo of the two dentists, a woman and a man in white coats, smiling"></div>

    <h1 class="practice-name">
      <span class="practice-name__main">Harlow</span>
      <span class="practice-name__sub">Brook Dentistry</span>
    </h1>

    <div class="web-band">
      <svg class="icon" width="46" height="46" viewBox="0 0 46 46" aria-hidden="true">
        <circle cx="23" cy="23" r="20" fill="none" stroke="#fff" stroke-width="4"/>
        <ellipse cx="23" cy="23" rx="8" ry="20" fill="none" stroke="#fff" stroke-width="3"/>
        <line x1="3" y1="23" x2="43" y2="23" stroke="#fff" stroke-width="3"/>
      </svg>
      <span class="web-band__url">Harlowbrookdentistry.example</span>
    </div>

    <div class="phone-band">
      <svg class="icon" width="46" height="46" viewBox="0 0 24 24" aria-hidden="true">
        <path fill="#17b31b" d="M6.6 10.8a15.1 15.1 0 0 0 6.6 6.6l2.2-2.2a1 1 0 0 1 1-.25 11.4 11.4 0 0 0 3.6.57 1 1 0 0 1 1 1V20a1 1 0 0 1-1 1A17 17 0 0 1 3 4a1 1 0 0 1 1-1h3.5a1 1 0 0 1 1 1c0 1.25.2 2.45.57 3.57a1 1 0 0 1-.25 1L6.6 10.8z"/>
        <path fill="none" stroke="#17b31b" stroke-width="1.8" stroke-linecap="round" d="M14 5.5a5 5 0 0 1 4.5 4.5M14 2a8.5 8.5 0 0 1 8 8"/>
      </svg>
      <span class="phone-band__number">(555) 847-1390</span>
    </div>
  </main>
</body>
</html>
```